Lanternfield Drinks business cards

We need a business card design for our new logo. The company is modern, progressive, professional, yet approachable. The key products are ready to drink bottles and cans of coffee based beverages.
These cards will be a critical part of the first impression made by our sales organization, business development team, and all external facing personnel.
Card can be a vertical or horizontal orientation.

Target Market(s)

Customers, suppliers, business partners

Industry/Entity Type

Business

Contact Information for Business Card

Business cards should feature Company Name and Logo.

Font styles to use
Serif

Colors

Designer to choose colors to be used in the design.

Requirements
Must have
• Strong readability of Name, phone #, mobile number and email address.
• Job title, website url, Street Address, and other details can be secondary level readability.
Nice to have
• High impact, simplistic quality design.
• Ok to utilize the 'H in the box' separate from the company name

```html
<!DOCTYPE html>
<html lang="en">
<head>
<meta charset="utf-8">
<title>Lanternfield Drinks — Business Cards</title>
<link href="https://fonts.googleapis.com/css2?family=PT+Serif:wght@400;700&display=swap" rel="stylesheet">
<style>
  :root {
    --bg: #a3a3a3;
    --orange: #e8572c;
    --orange-light: #f26a3b;
    --orange-dark: #d24a22;
    --white: #ffffff;
    --paper: #f7f7f7;
    --ink: #333333;
    --rule: #9a9a9a;
    --grey-wave: #8c8c8c;
  }
  * { margin: 0; padding: 0; box-sizing: border-box; }
  html, body { width: 1200px; height: 900px; overflow: hidden; }
  body {
    background: var(--bg);
    font-family: "PT Serif", Georgia, serif;
    position: relative;
  }
  .card {
    position: absolute;
    width: 640px;
    height: 366px;
    border-radius: 18px;
    overflow: hidden;
    box-shadow: 0 10px 24px rgba(0,0,0,0.28);
  }
  /* Back of card */
  .card-back {
    left: 200px; top: 52px;
    background: linear-gradient(120deg, var(--orange-dark), var(--orange-light));
    color: var(--white);
    display: flex; flex-direction: column; align-items: center; justify-content: center;
  }
  .back-mark {
    width: 74px; height: 74px;
    border: 5px solid var(--white);
    margin-bottom: 14px;
  }
  .back-name {
    font-size: 40px; font-weight: 700; letter-spacing: 2px; text-transform: uppercase;
  }
  .back-rule { width: 360px; height: 2px; background: var(--white); margin: 8px 0 30px; }
  .back-url { font-size: 16px; }

  /* Front of card */
  .card-front {
    left: 360px; top: 482px;
    background: linear-gradient(135deg, var(--white), var(--paper));
    color: var(--ink);
  }
  .front-swoosh { position: absolute; inset: 0; }
  .front-brand {
    position: absolute; left: 34px; top: 44px;
    display: flex; align-items: center; gap: 14px;
    color: var(--orange);
  }
  .front-mark { width: 62px; height: 62px; border: 5px solid var(--orange); }
  .front-name { font-size: 30px; font-weight: 700; text-transform: uppercase; letter-spacing: 1px; }
  .top-rule {
    position: absolute; left: 250px; right: 40px; top: 128px;
    height: 1px; background: var(--rule);
  }
  .address {
    position: absolute; right: 40px; top: 140px;
    text-align: right; font-size: 15px; line-height: 1.35;
  }
  .person { position: absolute; left: 40px; top: 160px; }
  .person-name { color: var(--orange); font-size: 28px; font-weight: 700; }
  .person-title { font-size: 18px; margin-top: 2px; }
  .person-rule { width: 250px; height: 1px; background: var(--rule); margin: 12px 0 10px; }
  .contact { list-style: none; font-size: 15px; }
  .contact li { display: flex; align-items: center; gap: 9px; margin-bottom: 5px; }
  .contact svg { width: 14px; height: 14px; fill: var(--orange); }
  .front-url {
    position: absolute; right: 28px; bottom: 22px;
    color: var(--white); font-size: 14px;
  }
</style>
</head>
<body>

  <section class="card card-back">
    <div class="back-mark"></div>
    <div class="back-name">Lanternfield Drinks</div>
    <div class="back-rule"></div>
    <div class="back-url">www.lanternfielddrinks.com</div>
  </section>

  <section class="card card-front">
    <svg class="front-swoosh" viewBox="0 0 640 366" preserveAspectRatio="none" aria-hidden="true">
      <path d="M250 366 C360 300 460 250 640 226 L640 244 C470 262 380 310 300 366 Z" fill="var(--grey-wave)"/>
      <path d="M300 366 C390 300 480 262 640 240 L640 366 Z" fill="var(--orange)"/>
    </svg>

    <div class="front-brand">
      <div class="front-mark"></div>
      <div class="front-name">Lanternfield Drinks</div>
    </div>
    <div class="top-rule"></div>
    <address class="address" style="font-style:normal">
      Level 5, 27 Harbour Lane<br>Fremont, VIC 3011
    </address>

    <div class="person">
      <div class="person-name">Daniel Avery</div>
      <div class="person-title">President</div>
      <div class="person-rule"></div>
      <ul class="contact">
        <li>
          <svg viewBox="0 0 24 24"><path d="M6.6 10.8a15 15 0 0 0 6.6 6.6l2.2-2.2a1 1 0 0 1 1-.25 11.4 11.4 0 0 0 3.6.57 1 1 0 0 1 1 1V20a1 1 0 0 1-1 1A17 17 0 0 1 3 4a1 1 0 0 1 1-1h3.5a1 1 0 0 1 1 1c0 1.25.2 2.45.57 3.6a1 1 0 0 1-.25 1z"/></svg>
          555 013 2468
        </li>
        <li>
          <svg viewBox="0 0 24 24"><path d="M2 5h20v14H2z M2 5l10 8 10-8" fill="var(--orange)"/><path d="M3 6l9 7 9-7" fill="none" stroke="#fff" stroke-width="1.6"/></svg>
          info@lanternfielddrinks.com
        </li>
      </ul>
    </div>

    <div class="front-url">www.lanternfield.co</div>
  </section>

</body>
</html>
```